Sophisticated, clean website reflecting my feminine, playful side to sell my abstract art,

I need a website no more than 3 pages to showcase my paintings, a little about me and some contact info. I do abstracts so looking for something a little edgy, yet feminine and current.
Updates

Hi there, These are some artists websites that I Iike: Marnelvoss.com (I like how airy it is) peterwallombry.com garethpolvens.com (I like how it scrolls) I'll need a place for a photo ( a headshot-i do not have it yet so I'll need to be able to upload that later) as well as an area for my bio. Also, it's important that I will be able to upload any new photos and descriptions easily so it should be user friendly. Lastly, I like in a sunny place so would like to have this seem upbeat and playful as that is how i like to paint. thanks-I'm trying to upload my photos now -

Target Market(s)

ppl ages 35-70 who want large scale art for their homes

Industry/Entity Type

art

Coding

Coded - Design and coding required

Number of Pages Required

3 page

Colors

Designer to choose colors to be used in the design.

Requirements
Must have
• photos of my art, a place for my bio, be easy to reach me. tasteful-nothing too "in your face" -my clients are pretty high end and organized. They like clean lines
Nice to have
• sophisticated background, muted tones in the back-similar clean font throughout-no cursive
Should not have
• too many dark areas. Too many blocks of color. Too serious.

```html
<!DOCTYPE html>
<html lang="en">
<head>
<meta charset="utf-8">
<title>Delia Marwood — Abstract Painter</title>
<link href="https://fonts.googleapis.com/css2?family=Questrial&family=Nunito+Sans:wght@300;400&display=swap" rel="stylesheet">
<style>
  :root {
    --page: #f0efed;
    --header: #ffffff;
    --ink: #3f3f3f;
    --ink-soft: #8a8a8a;
    --rule: #6f6f6f;
    --line: #d9d8d6;
    --hero-a: #3f8f3a;
    --hero-b: #1f7f7a;
    --hero-c: #d9dde0;
    --art-light: #dfe3e6;
    --art-warm: #cdb27a;
    --portrait: #f4f4f4;
  }
  * { margin: 0; padding: 0; box-sizing: border-box; }
  html, body { width: 1200px; height: 2988px; overflow: hidden; }
  body {
    position: relative;
    background: var(--page);
    color: var(--ink);
    font-family: "Nunito Sans", sans-serif;
    font-weight: 300;
  }
  .site-header {
    position: absolute; left: 0; top: 0; width: 1200px; height: 158px;
    background: var(--header);
  }
  .brand {
    position: absolute; top: 28px; left: 0; width: 1200px;
    text-align: center;
    font-family: "Questrial", sans-serif;
    font-size: 38px; letter-spacing: 1px; color: var(--ink);
  }
  .main-nav a {
    position: absolute; top: 116px;
    transform: translateX(-50%);
    font-family: "Questrial", sans-serif;
    font-size: 16px; color: var(--ink); text-decoration: none;
    white-space: nowrap;
  }
  .main-nav a.is-active::after {
    content: ""; position: absolute; left: 0; right: 0; bottom: -10px;
    height: 2px; background: var(--ink);
  }
  .hero {
    position: absolute; left: 0; top: 158px; width: 1200px; height: 658px;
    background: linear-gradient(115deg, var(--hero-c) 0%, var(--hero-a) 30%, var(--hero-b) 60%, #6a4a32 100%);
  }
  .slide-arrow { position: absolute; }
  .section-title {
    position: absolute;
    font-family: "Questrial", sans-serif;
    font-weight: 400; color: var(--ink);
    letter-spacing: 1px;
  }
  .title-rule { position: absolute; height: 2px; background: var(--rule); }
  .portrait {
    position: absolute; left: 82px; top: 968px; width: 355px; height: 401px;
    background: linear-gradient(180deg, #f7f7f7, #ececec);
  }
  .bio {
    position: absolute; left: 494px; top: 1072px; width: 652px;
    font-size: 18.5px; line-height: 28px; text-align: justify;
  }
  .bio p { margin-bottom: 14px; }
  .gallery-art {
    position: absolute; left: 163px; top: 1663px; width: 869px; height: 536px;
    background: linear-gradient(160deg, var(--art-light) 0%, #d6dbe0 45%, var(--art-warm) 100%);
  }
  .contact-intro {
    position: absolute; top: 2478px; left: 0; width: 1200px; text-align: center;
    font-size: 19px;
  }
  .contact-item {
    position: absolute; top: 2596px; width: 300px; transform: translateX(-50%);
    text-align: center;
  }
  .contact-item svg { display: block; margin: 0 auto; height: 50px; }
  .contact-label {
    margin-top: 12px;
    font-family: "Questrial", sans-serif; font-size: 19px; color: var(--ink-soft);
  }
  .contact-value {
    margin-top: 10px;
    font-family: "Questrial", sans-serif; font-size: 20px; color: #222;
  }
  .site-footer {
    position: absolute; left: 0; top: 2910px; width: 1200px; height: 78px;
    border-top: 1px solid var(--line);
    text-align: center; padding-top: 23px;
    font-family: "Questrial", sans-serif; font-size: 14px; color: var(--ink);
  }
</style>
</head>
<body>
  <header class="site-header">
    <div class="brand">DELIA MARWOOD</div>
    <nav class="main-nav">
      <a class="is-active" style="left:315px">HOME</a>
      <a style="left:494px">ABOUT ME</a>
      <a style="left:686px">GALLERY</a>
      <a style="left:888px">CONTACT ME</a>
    </nav>
  </header>

  <section class="hero" role="img" aria-label="Large abstract painting in green and teal tones"></section>
  <svg class="slide-arrow" style="left:22px;top:438px" width="28" height="48" viewBox="0 0 28 48"><path d="M24 2 L4 24 L24 46" fill="none" stroke="#fff" stroke-width="3"/></svg>
  <svg class="slide-arrow" style="left:1136px;top:438px" width="28" height="48" viewBox="0 0 28 48"><path d="M4 2 L24 24 L4 46" fill="none" stroke="#fff" stroke-width="3"/></svg>

  <div class="portrait" role="img" aria-label="Artist headshot placeholder"></div>
  <h2 class="section-title" style="left:494px;top:978px;font-size:52px">ABOUT ME</h2>
  <div class="title-rule" style="left:494px;top:1040px;width:260px"></div>
  <div class="bio">
    <p>Lorem ipsum dolor sit amet, consectetur adipiscing elit, sed do eiusmod tempor incididunt ut labore et dolore magna aliqua. Ut enim ad minim veniam, quis nostrud exercitation Lorem ipsum dolor sit amet, consectetur adipiscing elit, sed do eiusmod tempor incididunt ut labore et dolore</p>
    <p>Duis aute irure dolor in reprehenderit in voluptate velit esse cillum dolore eu fugiat nulla pariatur. Excepteur sint occaecat cupidatat non proident, sunt in culpa qui officia deserunt mollit anim id est laborum.</p>
    <p>Sed ut perspiciatis unde pariatur. Excepteur sint occaecat cupidatat non proident, sunt in culpa qui officia deserunt mollit anim id est laborum.</p>
  </div>

  <h2 class="section-title" style="left:0;width:1188px;text-align:center;top:1566px;font-size:48px">GALLERY</h2>
  <div class="title-rule" style="left:506px;top:1620px;width:180px"></div>
  <div class="gallery-art" role="img" aria-label="Gallery slide: abstract painting in pale blue, ochre and rust tones"></div>
  <svg class="slide-arrow" style="left:86px;top:1906px" width="28" height="48" viewBox="0 0 28 48"><path d="M24 2 L4 24 L24 46" fill="none" stroke="#888" stroke-width="3"/></svg>
  <svg class="slide-arrow" style="left:1086px;top:1906px" width="28" height="48" viewBox="0 0 28 48"><path d="M4 2 L24 24 L4 46" fill="none" stroke="#888" stroke-width="3"/></svg>

  <h2 class="section-title" style="left:0;width:1204px;text-align:center;top:2388px;font-size:52px">CONTACT ME</h2>
  <div class="title-rule" style="left:455px;top:2449px;width:307px"></div>
  <p class="contact-intro">Please get in touch with me on below details.</p>

  <div class="contact-item" style="left:257px">
    <svg viewBox="0 0 44 50" width="44"><rect x="2" y="12" width="40" height="28" fill="none" stroke="#888" stroke-width="1.5"/><path d="M2 12 L22 28 L42 12 M2 40 L17 25 M42 40 L27 25" fill="none" stroke="#888" stroke-width="1.5"/></svg>
    <div class="contact-label">Email me</div>
    <div class="contact-value">info@deliamarwood.com</div>
  </div>
  <div class="contact-item" style="left:547px">
    <svg viewBox="0 0 44 50" width="44"><path d="M8 6 L15 4 L20 15 L15 19 Q19 29 27 34 L31 29 L41 35 L39 42 Q34 46 24 40 Q10 31 5 16 Q4 10 8 6 Z" fill="none" stroke="#888" stroke-width="1.5"/><path d="M26 8 Q35 10 37 19 M25 14 Q30 15 31 20" fill="none" stroke="#888" stroke-width="1.5"/></svg>
    <div class="contact-label">Phone</div>
    <div class="contact-value">(555) 014 2290</div>
  </div>
  <div class="contact-item" style="left:785px">
    <svg viewBox="0 0 44 50" width="44"><circle cx="22" cy="26" r="18" fill="none" stroke="#888" stroke-width="1.5"/></svg>
    <div class="contact-label">Photo feed</div>
    <div class="contact-value">@dmarwoodart</div>
  </div>
  <div class="contact-item" style="left:995px">
    <svg viewBox="0 0 44 50" width="44"><rect x="6" y="9" width="32" height="32" fill="none" stroke="#888" stroke-width="1.5"/></svg>
    <div class="contact-label">Video feed</div>
    <div class="contact-value">@dmpainter</div>
  </div>

  <footer class="site-footer">© 2022 Delia Marwood&nbsp;&nbsp; All Rights Reserved</footer>
</body>
</html>
```